Zelmorra Capital LLC

Need Professional Business cards for New Investment Fund

Target Market(s)

High Quality investors

Industry/Entity Type

Financial

Contact Information for Business Card

Phone Number +1 555 284 6190
Name Lukas Varenko
Title Fund Manager
email lv@FundZelmorra.com
Website www.FundZelmorra.com

Colors

Designer to choose colors to be used in the design.

Requirements
Must have
• Must have our Logo and all of the above. Must be made so lettering and loge can be raised

```html
<!DOCTYPE html>
<html lang="en">
<head>
<meta charset="utf-8">
<title>Zelmorra Capital LLC – Business Card</title>
<link rel="stylesheet" href="https://fonts.googleapis.com/css2?family=Montserrat:wght@600&family=Raleway:wght@400;500&display=swap">
<style>
  :root {
    --stage: #1e1e1e;
    --stage-light: #333333;
    --brand-green: #58bb4a;
    --card-dark: #131417;
    --band-dark: #3e4a3c;
    --rule-green: #4fae41;
    --text-light: #ffffff;
    --text-soft: #e4e4e4;
  }
  * { margin: 0; padding: 0; box-sizing: border-box; }
  html, body { width: 1200px; height: 900px; overflow: hidden; }
  body {
    background: radial-gradient(ellipse at 70% 10%, var(--stage-light), var(--stage) 70%);
    font-family: "Raleway", sans-serif;
    position: relative;
  }
  .card {
    position: absolute;
    left: 250px;
    width: 700px;
    height: 400px;
    box-shadow: 0 14px 30px rgba(0,0,0,0.55);
    overflow: hidden;
  }
  .card--front { top: 35px; background: var(--brand-green); }
  .card--back { top: 465px; background: var(--card-dark); }

  .front-brand {
    position: absolute;
    left: 0; right: 0; top: 160px;
    display: flex; align-items: center; justify-content: center; gap: 16px;
  }
  .brand-mark { width: 26px; height: 26px; background: var(--text-light); flex: none; }
  .brand-name {
    font-family: "Raleway", sans-serif;
    font-weight: 500;
    font-size: 50px;
    letter-spacing: 5px;
    color: var(--text-light);
    white-space: nowrap;
  }
  .front-band {
    position: absolute;
    left: 268px; bottom: 0;
    width: 250px; height: 12px;
    background: var(--band-dark);
  }

  .back-brand {
    position: absolute; left: 70px; top: 70px;
    display: flex; align-items: center; gap: 12px;
  }
  .back-brand .brand-mark { width: 18px; height: 18px; background: var(--brand-green); }
  .back-brand .brand-name { font-size: 32px; letter-spacing: 3px; }

  .divider {
    position: absolute; left: 110px; top: 222px;
    width: 580px; height: 1.5px; background: var(--rule-green);
  }
  .holder { position: absolute; left: 95px; top: 250px; color: var(--text-light); }
  .holder-name {
    font-family: "Montserrat", sans-serif;
    font-weight: 600;
    font-size: 27px;
    letter-spacing: 1px;
    text-transform: uppercase;
    white-space: nowrap;
  }
  .holder-title { font-size: 21px; color: var(--text-soft); margin-top: 2px; }

  .contacts {
    position: absolute; right: 40px; top: 272px;
    list-style: none; text-align: right;
    color: var(--text-light); font-size: 22px; line-height: 35px;
  }
  .contacts li { display: flex; align-items: center; justify-content: flex-end; gap: 14px; white-space: nowrap; }
  .contacts svg { width: 18px; height: 18px; flex: none; }
  .accent-bar {
    position: absolute; left: 55px; bottom: 28px;
    width: 230px; height: 5px; background: var(--brand-green);
  }
</style>
</head>
<body>
  <section class="card card--front" aria-label="Card front">
    <div class="front-brand">
      <span class="brand-mark"></span>
      <span class="brand-name">ZELMORRA</span>
    </div>
    <div class="front-band"></div>
  </section>

  <section class="card card--back" aria-label="Card back">
    <div class="back-brand">
      <span class="brand-mark"></span>
      <span class="brand-name">ZELMORRA</span>
    </div>
    <div class="divider"></div>
    <div class="holder">
      <p class="holder-name">Lukas Varenko</p>
      <p class="holder-title">Title Fund Manager</p>
    </div>
    <ul class="contacts">
      <li>+1 555 284 6190
        <svg viewBox="0 0 24 24" aria-hidden="true"><path fill="var(--brand-green)" d="M6.6 10.8c1.4 2.8 3.8 5.1 6.6 6.6l2.2-2.2c.3-.3.7-.4 1-.2 1.1.4 2.3.6 3.6.6.6 0 1 .4 1 1V20c0 .6-.4 1-1 1C10.6 21 3 13.4 3 4c0-.6.4-1 1-1h3.5c.6 0 1 .4 1 1 0 1.3.2 2.5.6 3.6.1.3 0 .7-.2 1l-2.3 2.2z"/></svg>
      </li>
      <li>lv@FundZelmorra.com
        <svg viewBox="0 0 24 24" aria-hidden="true"><rect x="3" y="5" width="18" height="14" rx="1.5" fill="none" stroke="var(--brand-green)" stroke-width="2"/><path d="M3.5 6l8.5 7 8.5-7" fill="none" stroke="var(--brand-green)" stroke-width="2"/></svg>
      </li>
      <li>www.FundZelmorra.com
        <svg viewBox="0 0 24 24" aria-hidden="true"><g fill="none" stroke="var(--brand-green)" stroke-width="1.8"><circle cx="12" cy="12" r="9"/><ellipse cx="12" cy="12" rx="4" ry="9"/><path d="M3 12h18M4.5 7.5h15M4.5 16.5h15"/></g></svg>
      </li>
    </ul>
    <div class="accent-bar"></div>
  </section>
</body>
</html>
```